Illustrations, Icons and placement

Wire frame will describe it best, https://plavido.com/diagrams/kRtmWbNoQeprsLvx

With the direction of my mockups I am going to require illustrations with similarity to the mock up. I need icons for my slider and of course beautiful slides. It is not necessary to design the webpage, I know where I want to go with this, I really just need strong illustrations.

This is the first serious design submitted. I appreciate the obvious hard work. To be honest, this system is not great for designers to know exactly what I want but finding a designer that can put in the effort to get there is the trick.

I have locked in the front page design to something that is very accurately portrayed in the mockup. The reason why is the illustration I will using. Currently My mock up shows flower on a hill, i replace with an brightcrate illustration, see uploaded file to review... Also, colors are definatly what I am looking for but this ok for now. Your design is good..

Reason: my choice needs more time to finish the design before we begin

Target Market(s)

SaaS Consumer

Industry/Entity Type

Work

Requirements
Must have
• Display features in a nice slider like

http://www.drovelink.com/pebblegate/index.php

room in header for new illustration, see attachment
Should not have
• Traditional out dated designs that look like templates

```html
<!DOCTYPE html>
<html lang="en">
<head>
<meta charset="utf-8">
<title>Theme Builder</title>
<link rel="stylesheet" href="https://fonts.googleapis.com/css2?family=Tinos:wght@400;700&family=Source+Sans+3:wght@400;700&display=swap">
<style>
:root{
  --page:#0a0a0a;
  --panel:#0e0d0c;
  --glow:#3a220f;
  --nav-label:#9c8270;
  --nav-active:#e2766c;
  --icon:#000;
  --heading:#a9463e;
  --body:#8e7564;
  --stage:#030303;
  --tab-top:#ab4b57;
  --tab-bottom:#76222d;
  --tab-text:#ece6e8;
  --title:#8f6b2c;
  --video:#1b1b1b;
  --progress:#a3434d;
}
*{margin:0;padding:0;box-sizing:border-box}
html,body{width:1200px;height:901px;overflow:hidden;background:var(--page)}
body{position:relative;font-family:"Source Sans 3",sans-serif}
.nav{position:absolute;left:107px;top:0;width:958px;height:136px;
  background:linear-gradient(to bottom,#0d0c0b 0%,#120d09 55%,var(--glow) 100%);
  box-shadow:0 10px 30px rgba(40,22,8,.25)}
.nav::after{content:"";position:absolute;left:0;right:0;bottom:0;height:70px;
  background:linear-gradient(to bottom,rgba(10,10,10,0),rgba(10,10,10,.65))}
.nav-item{position:absolute;top:0;width:150px;margin-left:-75px;text-align:center;z-index:1}
.nav-item svg{display:block;margin:0 auto;filter:drop-shadow(0 0 8px rgba(120,70,30,.35))}
.nav-label{position:absolute;left:0;right:0;font-family:"Tinos",serif;font-weight:700;font-size:15px;line-height:18px;color:var(--nav-label)}
.nav-item.is-active .nav-label{color:var(--nav-active)}
.monitor{position:absolute;left:107px;top:202px;width:391px;height:314px;
  background:linear-gradient(to bottom,#2a2a2a 0%,#1a1a1a 70%,#9a9a9a 82%,#d8d8d8 100%);
  border-radius:8px}
.divider{position:absolute;left:541px;top:185px;width:3px;height:360px;
  background:linear-gradient(to bottom,transparent,#6b4a38 50%,transparent)}
.feature{position:absolute;width:230px}
.feature h3{font-family:"Tinos",serif;font-weight:700;font-size:19px;line-height:22px;color:var(--heading);letter-spacing:.2px}
.feature p{margin-top:11px;font-size:15px;line-height:23px;color:var(--body)}
.stage{position:absolute;left:107px;top:568px;width:958px;height:360px;border-radius:14px;
  background:linear-gradient(to bottom,var(--stage) 70%,#1d1209 100%)}
.tab{position:absolute;top:586px;width:60px;height:330px;border-radius:3px 3px 0 0;
  background:linear-gradient(to bottom,var(--tab-top),var(--tab-bottom))}
.tab span{position:absolute;left:50%;bottom:8px;transform-origin:0 0;
  transform:rotate(-90deg) translate(0,-50%);white-space:nowrap;
  font-weight:700;font-size:22px;line-height:26px;color:var(--tab-text);
  text-shadow:0 1px 2px rgba(0,0,0,.6)}
.slide-title{position:absolute;left:293px;top:595px;font-family:"Tinos",serif;font-size:24px;color:var(--title)}
.player{position:absolute;left:364px;top:652px;width:382px;height:208px;background:var(--video)}
.player svg{display:block}
</style>
</head>
<body>
<nav class="nav">
  <div class="nav-item" style="left:128px">
    <svg width="112" height="70" viewBox="0 0 112 70"><g fill="#000">
      <circle cx="28" cy="17" r="14"/><path d="M2 68 Q2 34 28 34 Q54 34 54 68Z"/>
      <circle cx="82" cy="17" r="14"/><path d="M56 68 Q56 34 82 34 Q108 34 108 68Z"/></g></svg>
    <div class="nav-label" style="top:88px">Collaborate</div>
  </div>
  <div class="nav-item" style="left:271px">
    <svg width="80" height="70" viewBox="0 0 80 70"><g fill="#000">
      <circle cx="28" cy="17" r="14"/><path d="M4 68 Q4 34 28 34 Q52 34 52 68Z"/>
      <circle cx="58" cy="26" r="9" fill="none" stroke="#000" stroke-width="4"/>
      <path d="M64 32 L74 42" stroke="#000" stroke-width="5"/></g></svg>
    <div class="nav-label" style="top:80px">Find<br>Professionals</div>
  </div>
  <div class="nav-item is-active" style="left:408px">
    <svg width="70" height="70" viewBox="0 0 70 70">
      <defs><linearGradient id="can" x1="0" y1="0" x2="0" y2="1"><stop offset="0" stop-color="#ee8a80"/><stop offset="1" stop-color="#b84a44"/></linearGradient></defs>
      <rect x="10" y="6" width="44" height="54" rx="6" fill="url(#can)"/>
      <ellipse cx="32" cy="10" rx="22" ry="6" fill="#222"/>
      <path d="M10 10 h44 v12 q-4 4 -6 0 q-4 8 -8 0 q-6 6 -10 0 q-6 10 -10 0 q-6 4 -10 0Z" fill="#222"/>
      <ellipse cx="55" cy="60" rx="9" ry="4" fill="#b84a44"/></svg>
    <div class="nav-label" style="top:80px">Theme<br>Builder</div>
  </div>
  <div class="nav-item" style="left:549px">
    <svg width="80" height="70" viewBox="0 0 80 70"><g fill="#000">
      <ellipse cx="40" cy="10" rx="38" ry="9"/>
      <path d="M2 14 q38 16 76 0 v12 q-38 16 -76 0Z"/>
      <path d="M2 31 q38 16 76 0 v12 q-38 16 -76 0Z"/>
      <path d="M2 48 q38 16 76 0 v10 q-38 16 -76 0Z"/></g></svg>
    <div class="nav-label" style="top:89px">Hosting</div>
  </div>
  <div class="nav-item" style="left:690px">
    <svg width="72" height="70" viewBox="0 0 72 70"><g stroke="#000" stroke-linecap="round">
      <path d="M12 12 L60 60" stroke-width="10"/>
      <path d="M58 10 L14 56" stroke-width="9"/></g>
      <circle cx="60" cy="12" r="11" fill="#000"/><circle cx="64" cy="8" r="5" fill="#0e0d0c"/>
      <rect x="4" y="4" width="16" height="12" fill="#000" transform="rotate(45 12 10)"/></svg>
    <div class="nav-label" style="top:80px">Developer<br>Tools</div>
  </div>
  <div class="nav-item" style="left:829px">
    <svg width="70" height="70" viewBox="0 0 70 70"><g fill="#000" stroke="#000" stroke-width="3">
      <circle cx="35" cy="35" r="7"/>
      <path d="M35 28V6M35 42V64M28 35H6M42 35H64M30 30L14 14M40 30L56 14M30 40L14 56M40 40L56 56"/>
      <path d="M35 2l-5 7h10zM35 68l-5-7h10zM2 35l7-5v10zM68 35l-7-5v10z" stroke="none"/></g></svg>
    <div class="nav-label" style="top:91px">Distributions</div>
  </div>
</nav>

<div class="monitor" role="img" aria-label="Desktop monitor showing a theme preview"></div>
<div class="divider"></div>

<section class="feature" style="left:585px;top:207px"><h3>EASILY PERSONALIZE</h3>
  <p>Dictumst purus augue, a amet, lundium augue, cras, etiam dipice parturient augue, tempor cum pellentesque. Lectus</p></section>
<section class="feature" style="left:843px;top:207px"><h3>RAPID THEMEING</h3>
  <p>Sed est sed pulvinar montes arcu nec magna, turpis purus ridiculus. Integer lacus egestas.</p></section>
<section class="feature" style="left:585px;top:383px"><h3>INSTANT PREVIEW</h3>
  <p>Dictumst purus augue, a amet, lundium augue, cras, etiam adipiscing parturient augue, tempor cum pellentesque.</p></section>
<section class="feature" style="left:840px;top:383px"><h3>SEO FRIENDLY CODE</h3>
  <p>Dictumst purus augue, a amet, lundium augue, cras, etiam adipiscing parturient augue, tempor cum pellentesque.</p></section>

<div class="stage"></div>
<div class="tab" style="left:142px"><span>The Theme Builder System</span></div>
<div class="tab" style="left:207px"><span>Personalize With Images</span></div>
<div class="tab" style="left:846px"><span>Drag &amp; Drop Interface</span></div>
<div class="tab" style="left:911px"><span>Sliding Adjustments</span></div>
<div class="tab" style="left:975px"><span>CSS Editing</span></div>

<h2 class="slide-title">Personalize With Images</h2>
<div class="player">
  <svg width="382" height="208" viewBox="0 0 382 208">
    <path d="M170 81 L213 105 L170 130Z" fill="#000"/>
    <rect x="8" y="175" width="363" height="24" rx="4" fill="#000"/>
    <rect x="17" y="181" width="3" height="11" fill="#a3434d"/><rect x="23" y="181" width="3" height="11" fill="#a3434d"/>
    <path d="M34 184h3l5-4v13l-5-4h-3z" fill="#a3434d"/>
    <rect x="53" y="183" width="283" height="6" rx="3" fill="#a3434d"/>
    <circle cx="354" cy="186" r="6" fill="none" stroke="#a3434d" stroke-width="2"/>
    <path d="M354 177v4M354 191v4M345 186h4M359 186h4" stroke="#a3434d" stroke-width="2"/>
  </svg>
</div>
</body>
</html>
```